Zielgruppe
Immobilienmakler
Aufgabenstellung
Top moderne hochwertige Visitenkate, wir hätten gerne eine sehr hochwertig moderne Visitenkarte mit Bild vom Mitarbeiter... Anbei habe ich die alte Visitenkarte die ich sehr kindlich finde... Es sollte jetzt sehr exklusive aussehen. Alle Daten können von der alten Visitenkarte übernommen werden.. danke

```html
<!DOCTYPE html>
<html lang="de">
<head>
<meta charset="utf-8">
<title>Velta Agentur – Visitenkarte</title>
<link href="https://fonts.googleapis.com/css2?family=Ubuntu:wght@400;500;700&display=swap" rel="stylesheet">
<style>
  :root {
    --backdrop: #5c5d5f;
    --card: #ffffff;
    --brand-green: #1b8a43;
    --ink: #2b2b2b;
    --photo-light: #eef0f3;
    --photo-mid: #c9cdd3;
  }
  * { box-sizing: border-box; margin: 0; padding: 0; }
  html, body {
    width: 1200px; height: 764px; overflow: hidden;
    background: var(--backdrop);
    font-family: "Ubuntu", sans-serif;
    color: var(--ink);
  }
  .canvas { position: relative; width: 1200px; height: 764px; }
  .card {
    position: absolute; top: 290px;
    width: 486px; height: 314px;
    background: var(--card);
    box-shadow: 0 4px 14px rgba(0,0,0,.35);
    overflow: hidden;
  }
  .card--front { left: 88px; }
  .card--back { left: 617px; }

  .company-name {
    position: absolute;
    font-weight: 700; color: var(--ink);
    white-space: nowrap; line-height: 1;
  }
  .card--front .company-name { right: 36px; top: 150px; font-size: 50px; }
  .card--back .company-name { right: 43px; top: 30px; font-size: 28px; }

  .address {
    position: absolute; right: 43px; top: 80px;
    text-align: right; font-size: 14px; line-height: 17px; font-style: normal;
  }
  .contact {
    position: absolute; left: 47px; top: 124px;
    display: grid; grid-template-columns: 54px auto;
    font-size: 13.5px; line-height: 17px;
  }
  .name-band {
    position: absolute; left: 0; top: 207px;
    width: 340px; height: 29px;
    background: var(--brand-green);
  }
  .name-band__name {
    position: absolute; left: 47px; top: 3px;
    color: #fff; font-size: 18px; line-height: 22px;
  }
  .role {
    position: absolute; left: 47px; top: 244px;
    font-size: 13.5px; line-height: 17.5px;
  }
  .portrait {
    position: absolute; left: 332px; top: 158px;
    width: 120px; height: 120px; border-radius: 50%;
    background: radial-gradient(circle at 50% 40%, var(--photo-light) 0%, var(--photo-mid) 100%);
    box-shadow: 0 1px 6px rgba(0,0,0,.25);
    border: 3px solid #fff;
  }
</style>
</head>
<body>
<div class="canvas">
  <section class="card card--front">
    <div class="company-name">Velta Agentur</div>
  </section>

  <section class="card card--back">
    <div class="company-name">Velta Agentur</div>
    <address class="address">Lindenweg 12<br>6830 Rankweil</address>
    <div class="contact">
      <span>Telefon</span><span>+43 5500 12 345 67</span>
      <span>Mobil</span><span>+43 660 4418 270</span>
      <span>E-Mail</span><span>lorenz@velta-agentur.com</span>
      <span>Web</span><span>www.velta-agentur.com</span>
    </div>
    <div class="name-band"><div class="name-band__name">Lorenz Hafner</div></div>
    <div class="role">Dipl. Immobilienmanager<br>Geschäftsführer</div>
    <div class="portrait" role="img" aria-label="Porträtfoto des Mitarbeiters im weißen Hemd"></div>
  </section>
</div>
</body>
</html>
```